Honey Company from Florida Needs Sweet and Buzz-worthy Site

Website Requests:
-Deluxe 5-Page Website with SSL-Secure Online Store (Shopify)
-High-end imagery to appeal to a discerning consumer
-Detailed verbiage with strong SEO and easy readability
-Design principles: simple, chic, luxe, earthy
Pages:
1. Home {Local, Raw American Honey from Florida}
2. The Hive
> About Us
>Meet the Beekeepers
3. Buy Honey
> Shopify retail store
4. The Buzz {News, Recipes & More}
> Blog
5. Contact Us {We're Buzzin' to Meet You}
> Store Hours
> Phone Number
> Address
> Quick Contact Form
Attachments: Web design notes, Logo, Color Codes, Inspiration Photos
Target Market(s)
High-end honey consumer in the U.S.
Industry/Entity Type
Upscale honey enthusiasts; direct to consumer sales.
Coding
Coded - Design and coding required
Number of Pages Required
5+ page
Requirements
Must have
- Upscale look and feel, easy usability for quick sales.

```html
<!DOCTYPE html>
<html lang="en">
<head>
<meta charset="utf-8">
<title>Golden Comb Co. — Home page layouts</title>
<link href="https://fonts.googleapis.com/css2?family=Merriweather:wght@400;700&family=Montserrat:wght@400;500;600&display=swap" rel="stylesheet">
<style>
:root{
  --backdrop:#ececec;
  --white:#ffffff;
  --ink:#1e1b1b;
  --body:#6b6664;
  --gold:#e3b63c;
  --band:#edcf69;
  --cream:#f5f3ee;
  --footer:#231f20;
  --footer-text:#e9e6e2;
  --line:#d9d4cc;
}
*{box-sizing:border-box;margin:0;padding:0}
html,body{width:840px;height:1200px;overflow:hidden;background:var(--backdrop)}
.stage{position:absolute;left:0;top:0;width:1607px;height:2296px;transform:scale(0.52271);transform-origin:0 0;background:var(--backdrop)}
.page{position:absolute;width:643px;background:var(--white);box-shadow:0 12px 40px rgba(0,0,0,.16);font-family:"Montserrat",sans-serif;color:var(--ink);overflow:hidden}
.page--a{left:99px;top:158px;height:1981px}
.page--b{left:866px;top:160px;height:1976px}
.abs{position:absolute}
.serif{font-family:"Merriweather",serif}

/* header */
.header{position:absolute;left:0;top:0;width:643px;height:80px;background:var(--white)}
.brand{position:absolute;left:58px;top:22px;display:flex;align-items:center;gap:6px;font-family:"Merriweather",serif;font-weight:700;font-size:13px;color:var(--ink);line-height:1.1;width:110px}
.brand__dot{width:10px;height:10px;border-radius:50%;background:var(--gold);flex:none}
.search{position:absolute;left:295px;top:14px;width:165px;border-bottom:1px solid var(--line);font-size:8px;color:var(--body);padding:2px 2px 5px}
.search svg{position:absolute;right:2px;top:1px}
.account{position:absolute;left:476px;top:20px;font-family:"Merriweather",serif;font-size:8px;color:var(--ink);display:flex;gap:10px}
.account span{display:flex;align-items:center;gap:3px}
.nav{position:absolute;left:295px;top:53px;display:flex;gap:20px;font-family:"Merriweather",serif;font-size:9.5px;color:var(--ink)}
.nav .is-active{color:var(--gold)}

/* hero */
.hero{position:absolute;left:0;width:643px;overflow:hidden}
.hero__photo{position:absolute;inset:0}
.hero__title{position:absolute;font-family:"Merriweather",serif;font-weight:700;color:var(--white);letter-spacing:.5px}
.btn-outline{position:absolute;border:1px solid var(--white);color:var(--white);font-size:10px;font-weight:500;display:flex;align-items:center;justify-content:center;letter-spacing:.3px}
.hero__arrow{position:absolute;top:50%;margin-top:-9px}

/* sections */
.eyebrow{font-family:"Merriweather",serif;font-size:10px;color:var(--gold)}
.title{font-family:"Merriweather",serif;font-weight:700;font-size:18px;color:var(--ink);text-transform:uppercase}
.copy{font-size:7.6px;line-height:13.6px;color:var(--body)}
.copy p+p{margin-top:13px}
.center{text-align:center}
.btn-gold{position:absolute;border:1px solid var(--gold);color:var(--gold);font-size:8.5px;font-weight:500;display:flex;align-items:center;justify-content:center}

.band{position:absolute;left:0;width:643px;height:346px;background:var(--band)}
.band__photo{position:absolute;left:0;top:0;width:268px;height:346px;background:linear-gradient(135deg,#8b8a6a 0%,#e9e8e3 35%,#cfcfc6 55%,#6b5a35 80%,#4a4128 100%)}
.band__text{position:absolute;left:313px;top:26px;width:275px;color:var(--white)}
.band__eyebrow{font-family:"Merriweather",serif;font-size:10px}
.band__title{font-family:"Merriweather",serif;font-weight:700;font-size:17px;line-height:24px;margin-top:8px}
.ticks{list-style:none;margin-top:18px}
.ticks li{position:relative;padding-left:16px;font-size:7.6px;line-height:13.8px;margin-bottom:13px}
.ticks svg{position:absolute;left:0;top:3px}
.band__btn{position:absolute;left:313px;width:89px;height:34px;border:1px solid var(--white);color:var(--white);font-size:8.5px;font-weight:500;display:flex;align-items:center;justify-content:center}
.band__mark{position:absolute;right:0;width:100px;height:70px;border-radius:50%;background:rgba(30,27,27,.14)}

.health{position:absolute;left:0;width:643px;height:318px}
.health__photo{position:absolute;left:339px;top:44px;width:244px;height:227px;background:linear-gradient(180deg,#aeb0bd 0%,#c6bcb4 45%,#8d866a 62%,#4b4636 78%,#3f3a2e 100%)}

.news{position:absolute;left:0;width:643px;height:375px;background:var(--cream)}
.card{position:absolute;top:100px;width:168px}
.card__photo{height:120px}
.card__title{font-size:10.5px;font-weight:500;margin-top:11px;color:var(--ink)}
.card__date{font-size:7.5px;color:var(--body);margin-top:6px;display:flex;align-items:center;gap:3px}
.card__text{font-size:7.5px;line-height:14px;color:var(--body);margin-top:8px}
.card__more{font-size:8.5px;font-weight:500;color:var(--gold);margin-top:7px}

.footer{position:absolute;left:0;width:643px;height:190px;background:var(--footer);color:var(--footer-text)}
.footer__head{font-size:10px;font-weight:500;text-transform:uppercase;letter-spacing:.3px}
.footer__line{font-size:7.8px;display:flex;align-items:center;gap:5px}
.field{position:absolute;left:311px;top:85px;width:272px;height:32px;background:var(--white);display:flex}
.field span{flex:1;font-size:8.5px;color:var(--body);padding:10px 12px}
.field b{width:32px;background:var(--gold);display:flex;align-items:center;justify-content:center}
.footer__rule{position:absolute;left:59px;top:137px;width:524px;height:1px;background:#4a4546}
.social{position:absolute;top:152px;width:23px;height:23px;border:1px solid var(--footer-text);border-radius:50%}
</style>
</head>
<body>
<div class="stage">

<!-- ================= Layout A ================= -->
<article class="page page--a">
  <header class="header">
    <div class="brand"><span class="brand__dot"></span>Golden Comb Co.</div>
    <div class="search">Search Products
      <svg width="9" height="9" viewBox="0 0 10 10"><circle cx="4" cy="4" r="3" fill="none" stroke="#e3b63c" stroke-width="1.3"/><path d="M6.3 6.3 9 9" stroke="#e3b63c" stroke-width="1.3"/></svg>
    </div>
    <div class="account">
      <span><svg width="8" height="8" viewBox="0 0 10 10"><circle cx="5" cy="3" r="2.2" fill="none" stroke="#e3b63c"/><path d="M1 9.5a4 4 0 0 1 8 0" fill="none" stroke="#e3b63c"/></svg>My Account</span>
      <span><svg width="9" height="8" viewBox="0 0 10 9"><path d="M0.5 2h9l-1 5h-7z" fill="none" stroke="#e3b63c"/></svg>$0.00</span>
    </div>
    <nav class="nav"><span class="is-active">Home</span><span>The Hive</span><span>Buy Honey</span><span>The Buzz</span><span>Contact</span></nav>
  </header>

  <section class="hero" style="top:80px;height:336px">
    <div class="hero__photo" role="img" aria-label="Honey jars and gift box on a table with warm festive lights behind" style="background:radial-gradient(circle at 25% 20%,#b8822c 0%,transparent 30%),radial-gradient(circle at 80% 70%,#9a4a16 0%,transparent 35%),linear-gradient(180deg,#2f5660 0%,#1e6f86 45%,#6a5538 75%,#d9d2c6 100%)"></div>
    <h1 class="hero__title" style="left:0;width:643px;top:56px;text-align:center;font-size:32px">BLESSED TO BEE-KEEP</h1>
    <div class="btn-outline" style="left:278px;top:107px;width:94px;height:33px">SHOP NOW</div>
    <svg class="hero__arrow" style="left:14px" width="10" height="18" viewBox="0 0 10 18"><path d="M8 2 2 9l6 7" fill="none" stroke="#fff" stroke-width="2"/></svg>
    <svg class="hero__arrow" style="right:14px" width="10" height="18" viewBox="0 0 10 18"><path d="M2 2l6 7-6 7" fill="none" stroke="#fff" stroke-width="2"/></svg>
  </section>

  <section class="abs" style="left:0;top:416px;width:643px;height:336px">
    <p class="eyebrow center" style="margin-top:34px">About</p>
    <h2 class="title center" style="margin-top:6px">Welcome to Golden Comb</h2>
    <div class="copy center" style="width:420px;margin:22px auto 0">
      <p>100% raw, unfiltered Florida honey straight from he beehives on his six-acre property, Golden Comb Honey Farm, 1180 Meadow Lane in Lakeview.</p>
      <p>Agricultural Company specializing in the Production of 100% Raw American Honey, and the Pollination of America’s food crops.</p>
      <p>Our Honey comes straight from our beehives to your table. No filtering, heating, or any funny stuff. Just All Natural, 100% Pure Florida Honey.</p>
      <p>Natural Wild Honey- flavors include Orange Blossom, Gallberry, Summer Wildflower, Winter Wildflower, and many more. Bee Pollen, Royal Jelly, and Bee venom. Bee removals are done by Marlon.</p>
      <p>Dupree, owner of Golden Comb Honey Farm, has about 1,200 beehives that he moves around to pollinate different plants.</p>
    </div>
  </section>

  <section class="band" style="top:752px">
    <div class="band__photo" role="img" aria-label="Beekeeper in a protective suit holding a honeycomb frame"></div>
    <div class="band__text">
      <p class="band__eyebrow">Importance of bees</p>
      <h2 class="band__title">“DON’T JUDGE A BEE BY ITS STINGER”</h2>
      <ul class="ticks">
        <li><svg width="8" height="8" viewBox="0 0 10 10"><circle cx="5" cy="5" r="5" fill="#fff"/><path d="M2.8 5.2 4.4 6.7 7.3 3.6" fill="none" stroke="#edcf69" stroke-width="1.4"/></svg>Hyper-efficient insects do play a vital role in agriculture. Almonds, for example, are almost entirely dependent on honeybee pollination.</li>
        <li><svg width="8" height="8" viewBox="0 0 10 10"><circle cx="5" cy="5" r="5" fill="#fff"/><path d="M2.8 5.2 4.4 6.7 7.3 3.6" fill="none" stroke="#edcf69" stroke-width="1.4"/></svg>“Over one-third of our entire diet is dependent on pollination from the honeybee. So, for every three bites of food you eat, you can thank the honeybee for one of those three bites,” Marlon says.</li>
        <li><svg width="8" height="8" viewBox="0 0 10 10"><circle cx="5" cy="5" r="5" fill="#fff"/><path d="M2.8 5.2 4.4 6.7 7.3 3.6" fill="none" stroke="#edcf69" stroke-width="1.4"/></svg>The state’s bees pollinate a variety of crops, from Florida blueberries to California almonds.</li>
      </ul>
    </div>
    <div class="band__btn" style="top:280px">READ MORE</div>
    <div class="band__mark" role="img" aria-label="Line drawing of a bee" style="top:262px"></div>
  </section>

  <section class="health" style="top:1098px">
    <div class="abs" style="left:59px;top:44px;width:265px">
      <p class="eyebrow">The health benefits of honey</p>
      <h2 class="title" style="line-height:25px;margin-top:8px">“Real local honey, really good for you”</h2>
      <div class="copy" style="margin-top:14px;line-height:14.6px">
        <p>Raw honey is loaded with antioxidants to protect your body from cell damage due to free radicals.</p>
        <p>Honey has been long known as a folk remedy to help heal burns and wounds due to its antibacterial and antifungal properties. Honey is also very well known to soothe a sore throat. Try taking a spoonful of honey and add it to hot tea if you feel like you have a cold. Honey can also help as a cough suppressant.</p>
      </div>
    </div>
    <div class="health__photo" role="img" aria-label="Field of beehives at sunset with trees on the horizon"></div>
  </section>

  <section class="news" style="top:1416px">
    <p class="eyebrow center" style="padding-top:36px">Social media posts</p>
    <h2 class="title center" style="margin-top:6px">Latest News</h2>
    <div class="card" style="left:59px"><div class="card__photo" role="img" aria-label="Honey jars displayed on a market table" style="background:linear-gradient(180deg,#4f6b3a,#8a5a22 55%,#e8e4dc)"></div><p class="card__title">Lorem ipsum dolor sit amet</p><p class="card__date"><svg width="7" height="7" viewBox="0 0 8 8"><rect x=".5" y="1.5" width="7" height="6" fill="none" stroke="#e3b63c"/></svg>Mar 8, 2022</p><p class="card__text">Nam libero tempore, cum soluta nobs est eligendi optio cumque nihil impe dit quo minus id quod..</p><p class="card__more">READ MORE</p></div>
    <div class="card" style="left:237px"><div class="card__photo" role="img" aria-label="Hands holding a smoking bee smoker" style="background:linear-gradient(135deg,#6d5a1c,#b98a3a 45%,#2c2418)"></div><p class="card__title">Lorem ipsum dolor sit amet</p><p class="card__date"><svg width="7" height="7" viewBox="0 0 8 8"><rect x=".5" y="1.5" width="7" height="6" fill="none" stroke="#e3b63c"/></svg>Mar 8, 2022</p><p class="card__text">Nam libero tempore, cum soluta nobs est eligendi optio cumque nihil impe dit quo minus id quod..</p><p class="card__more">READ MORE</p></div>
    <div class="card" style="left:415px"><div class="card__photo" role="img" aria-label="Rows of white beehive boxes in a grassy field" style="background:linear-gradient(180deg,#9fc0d8 0%,#c9b46c 35%,#e9dfb8 60%,#9b8748 100%)"></div><p class="card__title">Lorem ipsum dolor sit amet</p><p class="card__date"><svg width="7" height="7" viewBox="0 0 8 8"><rect x=".5" y="1.5" width="7" height="6" fill="none" stroke="#e3b63c"/></svg>Mar 8, 2022</p><p class="card__text">Nam libero tempore, cum soluta nobs est eligendi optio cumque nihil impe dit quo minus id quod..</p><p class="card__more">READ MORE</p></div>
  </section>

  <footer class="footer" style="top:1791px">
    <p class="footer__head abs" style="left:59px;top:38px">Contact us</p>
    <p class="footer__line abs" style="left:59px;top:63px"><svg width="7" height="7" viewBox="0 0 10 10"><path d="M2 1l2 2-1 1.5a6 6 0 0 0 2.5 2.5L7 6l2 2-1.5 1.5C4.5 9.5.5 5.5.5 2.5z" fill="#e3b63c"/></svg>(555) 014-2286</p>
    <p class="footer__line abs" style="left:59px;top:93px"><svg width="6" height="8" viewBox="0 0 8 10"><path d="M4 10S0 5.5 0 3.8a4 4 0 0 1 8 0C8 5.5 4 10 4 10z" fill="#e3b63c"/><circle cx="4" cy="3.8" r="1.4" fill="#231f20"/></svg>1180 Meadow Lane, Lakeview, FL 32000</p>
    <p class="footer__head abs" style="left:311px;top:38px">Sign-up for our emails</p>
    <p class="footer__line abs" style="left:311px;top:63px">Enter your email address to get updates from us</p>
    <div class="field"><span>Email Address</span><b><svg width="11" height="10" viewBox="0 0 11 10"><path d="M0 5h9M5.5 1 9.5 5 5.5 9" fill="none" stroke="#fff" stroke-width="2"/></svg></b></div>
    <div class="footer__rule"></div>
    <p class="footer__line abs" style="left:59px;top:159px">© 2021 Golden Comb. Privacy Policy | Terms &amp; Conditions</p>
    <span class="social" style="left:532px"></span><span class="social" style="left:560px"></span>
  </footer>
</article>

<!-- ================= Layout B ================= -->
<article class="page page--b">
  <header class="header" style="height:74px">
    <div class="brand"><span class="brand__dot"></span>Golden Comb Co.</div>
    <div class="search">Search Products
      <svg width="9" height="9" viewBox="0 0 10 10"><circle cx="4" cy="4" r="3" fill="none" stroke="#e3b63c" stroke-width="1.3"/><path d="M6.3 6.3 9 9" stroke="#e3b63c" stroke-width="1.3"/></svg>
    </div>
    <div class="account">
      <span><svg width="8" height="8" viewBox="0 0 10 10"><circle cx="5" cy="3" r="2.2" fill="none" stroke="#e3b63c"/><path d="M1 9.5a4 4 0 0 1 8 0" fill="none" stroke="#e3b63c"/></svg>My Account</span>
      <span><svg width="9" height="8" viewBox="0 0 10 9"><path d="M0.5 2h9l-1 5h-7z" fill="none" stroke="#e3b63c"/></svg>$0.00</span>
    </div>
    <nav class="nav"><span class="is-active">Home</span><span>The Hive</span><span>Buy Honey</span><span>The Buzz</span><span>Contact</span></nav>
  </header>

  <section class="hero" style="top:74px;height:324px">
    <div class="hero__photo" role="img" aria-label="Coastal town on green cliffs above a blue bay with a harbour" style="background:linear-gradient(180deg,#a9b8c6 0%,#5d7f95 14%,#2f5e7c 40%,#3f6a5a 65%,#8a9a84 100%),#2f5e7c"></div>
    <h1 class="hero__title" style="left:72px;top:80px;font-size:34px;line-height:43px">BLESSED<br>TO BEE-KEEP</h1>
    <div class="btn-outline" style="left:72px;top:184px;width:94px;height:32px">SHOP NOW</div>
    <svg class="hero__arrow" style="left:22px" width="10" height="18" viewBox="0 0 10 18"><path d="M8 2 2 9l6 7" fill="none" stroke="#fff" stroke-width="2"/></svg>
    <svg class="hero__arrow" style="right:22px" width="10" height="18" viewBox="0 0 10 18"><path d="M2 2l6 7-6 7" fill="none" stroke="#fff" stroke-width="2"/></svg>
  </section>

  <section class="abs" style="left:0;top:398px;width:643px;height:346px">
    <div class="abs" style="left:59px;top:36px;width:275px">
      <p class="eyebrow">About</p>
      <h2 class="title" style="margin-top:6px">Welcome to Golden Comb</h2>
      <div class="copy" style="margin-top:15px">
        <p>100% raw, unfiltered Florida honey straight from he beehives on his six-acre property, Golden Comb Honey Farm, 1180 Meadow Lane in Lakeview.</p>
        <p>Agricultural Company specializing in the Production of 100% Raw American Honey, and the Pollination of America’s food crops.</p>
        <p>Our Honey comes straight from our beehives to your table. No filtering, heating, or any funny stuff. Just All Natural, 100% Pure Florida Honey.</p>
      </div>
    </div>
    <div class="btn-gold" style="left:59px;top:263px;width:88px;height:34px">READ MORE</div>
    <div class="abs" role="img" aria-label="Open gift box holding three honey jars" style="left:362px;top:60px;width:238px;height:215px;background:linear-gradient(180deg,#d2c1a4 0%,#d2c1a4 12%,#4a3a2c 14%,#e5e0d8 45%,#b31e25 70%,#3f2f24 75%,#3f2f24 100%)"></div>
  </section>

  <section class="band" style="top:744px">
    <div class="band__photo" role="img" aria-label="Beekeeper in a protective suit holding a honeycomb frame"></div>
    <div class="band__text">
      <p class="band__eyebrow">Importance of bees</p>
      <h2 class="band__title">“DON’T JUDGE A BEE BY ITS STINGER”</h2>
      <ul class="ticks">
        <li><svg width="8" height="8" viewBox="0 0 10 10"><circle cx="5" cy="5" r="5" fill="#fff"/><path d="M2.8 5.2 4.4 6.7 7.3 3.6" fill="none" stroke="#edcf69" stroke-width="1.4"/></svg>Hyper-efficient insects do play a vital role in agriculture. Almonds, for example, are almost entirely dependent on honeybee pollination.</li>
        <li><svg width="8" height="8" viewBox="0 0 10 10"><circle cx="5" cy="5" r="5" fill="#fff"/><path d="M2.8 5.2 4.4 6.7 7.3 3.6" fill="none" stroke="#edcf69" stroke-width="1.4"/></svg>“Over one-third of our entire diet is dependent on pollination from the honeybee. So, for every three bites of food you eat, you can thank the honeybee for one of those three bites,” Marlon says.</li>
        <li><svg width="8" height="8" viewBox="0 0 10 10"><circle cx="5" cy="5" r="5" fill="#fff"/><path d="M2.8 5.2 4.4 6.7 7.3 3.6" fill="none" stroke="#edcf69" stroke-width="1.4"/></svg>The state’s bees pollinate a variety of crops, from Florida blueberries to California almonds.</li>
      </ul>
    </div>
    <div class="band__btn" style="top:280px">READ MORE</div>
    <div class="band__mark" role="img" aria-label="Line drawing of a bee" style="top:262px"></div>
  </section>

  <section class="health" style="top:1090px">
    <div class="abs" style="left:59px;top:44px;width:265px">
      <p class="eyebrow">The health benefits of honey</p>
      <h2 class="title" style="line-height:25px;margin-top:8px">“Real local honey, really good for you”</h2>
      <div class="copy" style="margin-top:14px;line-height:14.6px">
        <p>Raw honey is loaded with antioxidants to protect your body from cell damage due to free radicals.</p>
        <p>Honey has been long known as a folk remedy to help heal burns and wounds due to its antibacterial and antifungal properties. Honey is also very well known to soothe a sore throat. Try taking a spoonful of honey and add it to hot tea if you feel like you have a cold. Honey can also help as a cough suppressant.</p>
      </div>
    </div>
    <div class="health__photo" role="img" aria-label="Field of beehives at sunset with trees on the horizon"></div>
  </section>

  <section class="news" style="top:1408px">
    <p class="eyebrow center" style="padding-top:36px">Social media posts</p>
    <h2 class="title center" style="margin-top:6px">Latest News</h2>
    <div class="card" style="left:59px"><div class="card__photo" role="img" aria-label="Honey jars displayed on a market table" style="background:linear-gradient(180deg,#4f6b3a,#8a5a22 55%,#e8e4dc)"></div><p class="card__title">Lorem ipsum dolor sit amet</p><p class="card__date"><svg width="7" height="7" viewBox="0 0 8 8"><rect x=".5" y="1.5" width="7" height="6" fill="none" stroke="#e3b63c"/></svg>Mar 8, 2022</p><p class="card__text">Nam libero tempore, cum soluta nobs est eligendi optio cumque nihil impe dit quo minus id quod..</p><p class="card__more">READ MORE</p></div>
    <div class="card" style="left:237px"><div class="card__photo" role="img" aria-label="Hands holding a smoking bee smoker" style="background:linear-gradient(135deg,#6d5a1c,#b98a3a 45%,#2c2418)"></div><p class="card__title">Lorem ipsum dolor sit amet</p><p class="card__date"><svg width="7" height="7" viewBox="0 0 8 8"><rect x=".5" y="1.5" width="7" height="6" fill="none" stroke="#e3b63c"/></svg>Mar 8, 2022</p><p class="card__text">Nam libero tempore, cum soluta nobs est eligendi optio cumque nihil impe dit quo minus id quod..</p><p class="card__more">READ MORE</p></div>
    <div class="card" style="left:415px"><div class="card__photo" role="img" aria-label="Rows of white beehive boxes in a grassy field" style="background:linear-gradient(180deg,#9fc0d8 0%,#c9b46c 35%,#e9dfb8 60%,#9b8748 100%)"></div><p class="card__title">Lorem ipsum dolor sit amet</p><p class="card__date"><svg width="7" height="7" viewBox="0 0 8 8"><rect x=".5" y="1.5" width="7" height="6" fill="none" stroke="#e3b63c"/></svg>Mar 8, 2022</p><p class="card__text">Nam libero tempore, cum soluta nobs est eligendi optio cumque nihil impe dit quo minus id quod..</p><p class="card__more">READ MORE</p></div>
  </section>

  <footer class="footer" style="top:1783px;height:193px">
    <p class="footer__head abs" style="left:59px;top:38px">Contact us</p>
    <p class="footer__line abs" style="left:59px;top:63px"><svg width="7" height="7" viewBox="0 0 10 10"><path d="M2 1l2 2-1 1.5a6 6 0 0 0 2.5 2.5L7 6l2 2-1.5 1.5C4.5 9.5.5 5.5.5 2.5z" fill="#e3b63c"/></svg>(555) 014-2286</p>
    <p class="footer__line abs" style="left:59px;top:93px"><svg width="6" height="8" viewBox="0 0 8 10"><path d="M4 10S0 5.5 0 3.8a4 4 0 0 1 8 0C8 5.5 4 10 4 10z" fill="#e3b63c"/><circle cx="4" cy="3.8" r="1.4" fill="#231f20"/></svg>1180 Meadow Lane, Lakeview, FL 32000</p>
    <p class="footer__head abs" style="left:311px;top:38px">Sign-up for our emails</p>
    <p class="footer__line abs" style="left:311px;top:63px">Enter your email address to get updates from us</p>
    <div class="field"><span>Email Address</span><b><svg width="11" height="10" viewBox="0 0 11 10"><path d="M0 5h9M5.5 1 9.5 5 5.5 9" fill="none" stroke="#fff" stroke-width="2"/></svg></b></div>
    <div class="footer__rule"></div>
    <p class="footer__line abs" style="left:59px;top:159px">© 2021 Golden Comb. Privacy Policy | Terms &amp; Conditions</p>
    <span class="social" style="left:532px"></span><span class="social" style="left:560px"></span>
  </footer>
</article>

</div>
</body>
</html>
```